Pipe Repair Clamps

A double side A4 showing our pipe repair clamps for stopping leaking pipes within seconds. For water , sewage companies, hotels, malls, airports, hosptals, facilities management companies and district cooling companies. Reverse side will show a size chart. Examples of product uploaded

```html
<!DOCTYPE html>
<html lang="en">
<head>
<meta charset="utf-8">
<title>Pipe Repair Clamps – Size Chart</title>
<link href="https://fonts.googleapis.com/css2?family=Roboto:wght@400;500;700;900&display=swap" rel="stylesheet">
<style>
:root{
  --sky-top:#e6f1f8;
  --sky-mid:#b9dcf0;
  --sky-low:#8fc6e6;
  --sea:#3f8fb4;
  --panel:#000000;
  --tile:#4f7fc4;
  --stripe:#4f7fc4;
  --orange:#d47a2c;
  --head:#c0602e;
  --teal:#1aa3c8;
  --ink:#111111;
  --white:#ffffff;
  --row-a:rgba(255,255,255,.55);
  --row-b:rgba(200,235,225,.45);
}
*{margin:0;padding:0;box-sizing:border-box}
html,body{width:927px;height:1200px;overflow:hidden}
body{font-family:'Roboto',Arial,sans-serif;color:var(--ink);background:var(--white)}
.sheet{position:relative;width:927px;height:1200px;overflow:hidden;
  background:linear-gradient(180deg,var(--sky-top) 0%,var(--sky-mid) 45%,var(--sky-low) 70%,var(--sky-mid) 85%)}
.skyline{position:absolute;left:0;top:790px;width:927px;height:230px;
  background:linear-gradient(180deg,rgba(143,198,230,0) 0%,#9cc3d8 30%,#6f9fb8 62%,var(--sea) 78%,#2d7ea6 100%)}
.stripe{position:absolute;left:0;top:1020px;width:927px;height:8px;background:var(--stripe)}
.footer{position:absolute;left:0;top:1028px;width:927px;height:172px;background:var(--white)}

.size-chart{position:absolute;left:44px;top:68px;width:534px;border-collapse:collapse;table-layout:fixed;font-size:7.6px;text-align:center}
.size-chart th{background:var(--head);color:var(--white);font-weight:400;border-right:1px solid rgba(255,255,255,.45);line-height:1.4;font-size:7.2px}
.size-chart thead tr:first-child th{height:32px}
.size-chart thead tr:last-child th{height:28px;border-top:1px solid rgba(255,255,255,.45)}
.size-chart td{height:17.3px;padding:0}
.size-chart tbody tr:nth-child(odd) td{background:var(--row-a)}
.size-chart tbody tr:nth-child(even) td{background:var(--row-b)}
.size-chart tbody tr:last-child td{border-bottom:2px solid #2f9a6a}
.chart-note{position:absolute;left:52px;top:746px;font-size:7.2px}

.side-panel{position:absolute;left:624px;top:0;width:268px;height:1096px;background:var(--panel)}
.side-base{position:absolute;left:624px;top:1134px;width:268px;height:66px;background:var(--panel)}
.side-rule{position:absolute;left:624px;top:1124px;width:268px;height:9px;background:var(--orange)}
.brand{position:absolute;left:624px;top:110px;width:268px;text-align:center;color:var(--orange);font-weight:900}
.brand-dot{display:block;width:56px;height:56px;border-radius:50%;background:var(--orange);margin:0 auto 18px}
.brand-name{display:block;font-size:46px;line-height:1;letter-spacing:1px}

.tile{position:absolute;left:622px;width:272px;background:var(--tile);color:var(--white);font-weight:700;font-size:42px;line-height:52px;text-align:center;display:flex;align-items:center;justify-content:center}
.tile-capping{top:304px;height:78px}
.tile-fittings{top:390px;height:90px}
.tile-flow{top:488px;height:124px}

.about{position:absolute;left:642px;top:634px;width:238px;color:var(--white);font-size:18.4px;line-height:21.8px}
.about p+p{margin-top:21.8px}

.call{position:absolute;left:0;width:668px;text-align:center}
.call-label{top:1046px;font-size:31px;font-weight:500;color:var(--ink)}
.call-number{top:1074px;font-size:68px;font-weight:700;color:var(--orange);letter-spacing:1px}
.call-web{top:1148px;font-size:20px;font-weight:700;color:var(--teal);letter-spacing:6px}
</style>
</head>
<body>
<main class="sheet">
  <div class="skyline" role="img" aria-label="Photograph of a modern city skyline with high-rise towers across a blue sea"></div>
  <div class="stripe"></div>
  <div class="footer"></div>

  <table class="size-chart">
    <colgroup>
      <col style="width:44px"><col style="width:82px"><col style="width:40px"><col style="width:42px"><col style="width:31px"><col style="width:30px"><col style="width:31px"><col style="width:85px"><col style="width:69px"><col style="width:36px"><col style="width:44px">
    </colgroup>
    <thead>
      <tr><th>Pipe O.D.</th><th>O.D.Range</th><th>Ship</th><th>Industry</th><th colspan="5">Dimensions</th><th>Screws</th><th>Screw<br>Torque</th></tr>
      <tr><th>OD<br>(mm)</th><th>ODmin–ODmax<br>(mm)</th><th>PN<br>(mm)</th><th>WP<br>(bar)</th><th>C<br>(mm)</th><th>l1<br>(mm)</th><th>l2<br>(mm)</th><th>D<br>(mm)</th><th>H<br>(mm)</th><th>M</th><th>Nm</th></tr>
    </thead>
    <tbody>
      <tr><td>21.7</td><td>21–23</td><td>16</td><td>32</td><td>3</td><td>57</td><td>–</td><td>35</td><td>50</td><td>6</td><td>15</td></tr>
      <tr><td>25</td><td>24.5–25.5</td><td>16</td><td>32</td><td>3</td><td>57</td><td>–</td><td>50</td><td>70</td><td>6</td><td>15</td></tr>
      <tr><td>27.2</td><td>26–28</td><td>16</td><td>32</td><td>3</td><td>57</td><td>–</td><td>50</td><td>70</td><td>6</td><td>15</td></tr>
      <tr><td>32</td><td>31.5–32.5</td><td>16</td><td>32</td><td>3</td><td>57</td><td>–</td><td>55</td><td>75</td><td>6</td><td>15</td></tr>
      <tr><td>34</td><td>33–35</td><td>16</td><td>32</td><td>3</td><td>57</td><td>–</td><td>55</td><td>75</td><td>6</td><td>15</td></tr>
      <tr><td>40</td><td>39.5–41.5</td><td>16</td><td>32</td><td>5</td><td>57</td><td>–</td><td>55</td><td>75</td><td>6</td><td>15</td></tr>
      <tr><td>42</td><td>42–44</td><td>16</td><td>32</td><td>5</td><td>57</td><td>–</td><td>65</td><td>85</td><td>6</td><td>15</td></tr>
      <tr><td>44.5</td><td>44–45.1</td><td>16</td><td>32</td><td>5</td><td>57</td><td>–</td><td>65</td><td>85</td><td>6</td><td>15</td></tr>
      <tr><td>48.6</td><td>47–49</td><td>16</td><td>32</td><td>5</td><td>57</td><td>100</td><td>70</td><td>90</td><td>6</td><td>15</td></tr>
      <tr><td>54</td><td>53.3–54.6</td><td>16</td><td>32</td><td>5</td><td>57</td><td>100</td><td>70</td><td>90</td><td>8</td><td>30</td></tr>
      <tr><td>57</td><td>56.3–57.7</td><td>16</td><td>32</td><td>5</td><td>57</td><td>100</td><td>50</td><td>100</td><td>8</td><td>30</td></tr>
      <tr><td>60.3</td><td>59–62</td><td>16</td><td>32</td><td>5</td><td>80</td><td>139</td><td>85</td><td>105</td><td>8</td><td>30</td></tr>
      <tr><td>63</td><td>62.2–63.9</td><td>16</td><td>32</td><td>5</td><td>80</td><td>139</td><td>85</td><td>105</td><td>8</td><td>30</td></tr>
      <tr><td>76.1</td><td>75–78</td><td>14</td><td>28</td><td>5</td><td>80</td><td>139</td><td>100</td><td>120</td><td>8</td><td>30</td></tr>
      <tr><td>79.9</td><td>78.8–80.8</td><td>14</td><td>28</td><td>5</td><td>80</td><td>139</td><td>100</td><td>120</td><td>8</td><td>30</td></tr>
      <tr><td>88.9</td><td>88–92</td><td>14</td><td>28</td><td>5</td><td>107</td><td>203</td><td>110</td><td>130</td><td>10</td><td>50</td></tr>
      <tr><td>108</td><td>106–110</td><td>14</td><td>28</td><td>5</td><td>107</td><td>203</td><td>130</td><td>150</td><td>10</td><td>50</td></tr>
      <tr><td>110</td><td>108.9–111.2</td><td>14</td><td>28</td><td>5</td><td>107</td><td>203</td><td>130</td><td>150</td><td>10</td><td>50</td></tr>
      <tr><td>114.3</td><td>112–116</td><td>14</td><td>28</td><td>5</td><td>107</td><td>203</td><td>135</td><td>155</td><td>10</td><td>50</td></tr>
      <tr><td>118</td><td>116.6–119.2</td><td>14</td><td>28</td><td>5</td><td>107</td><td>203</td><td>140</td><td>160</td><td>10</td><td>50</td></tr>
      <tr><td>125</td><td>123.6–126.5</td><td>14</td><td>28</td><td>5</td><td>107</td><td>203</td><td>150</td><td>185</td><td>10</td><td>50</td></tr>
      <tr><td>133</td><td>131.5–134.4</td><td>14</td><td>28</td><td>5</td><td>107</td><td>203</td><td>160</td><td>190</td><td>10</td><td>50</td></tr>
      <tr><td>140</td><td>137–143</td><td>14</td><td>28</td><td>5</td><td>116</td><td>203</td><td>165</td><td>195</td><td>12</td><td>80</td></tr>
      <tr><td>159</td><td>157–161</td><td>12</td><td>24</td><td>10</td><td>116</td><td>203</td><td>185</td><td>215</td><td>12</td><td>80</td></tr>
      <tr><td>165.2</td><td>163.3–166.7</td><td>12</td><td>24</td><td>10</td><td>116</td><td>203</td><td>190</td><td>210</td><td>12</td><td>80</td></tr>
      <tr><td>168</td><td>166–170</td><td>12</td><td>24</td><td>10</td><td>116</td><td>203</td><td>195</td><td>225</td><td>12</td><td>80</td></tr>
      <tr><td>170</td><td>168.2–171.9</td><td>12</td><td>24</td><td>10</td><td>116</td><td>203</td><td>195</td><td>225</td><td>14</td><td>100</td></tr>
      <tr><td>200</td><td>198.2–201.5</td><td>8</td><td>16</td><td>10</td><td>116</td><td>203</td><td>240</td><td>270</td><td>14</td><td>100</td></tr>
      <tr><td>219</td><td>217–221</td><td>8</td><td>16</td><td>10</td><td>155</td><td>255</td><td>250</td><td>280</td><td>14</td><td>100</td></tr>
      <tr><td>250</td><td>250–254</td><td>8</td><td>16</td><td>10</td><td>155</td><td>255</td><td>285</td><td>315</td><td>14</td><td>100</td></tr>
      <tr><td>273</td><td>271–275</td><td>8</td><td>16</td><td>10</td><td>155</td><td>255</td><td>305</td><td>335</td><td>14</td><td>100</td></tr>
      <tr><td>315</td><td>313–317</td><td>7</td><td>14</td><td>10</td><td>155</td><td>255</td><td>340</td><td>375</td><td>14</td><td>100</td></tr>
      <tr><td>325</td><td>323–327</td><td>7</td><td>14</td><td>10</td><td>155</td><td>255</td><td>360</td><td>390</td><td>14</td><td>100</td></tr>
      <tr><td>355.6</td><td>354–358</td><td>7</td><td>14</td><td>10</td><td>155</td><td>255</td><td>385</td><td>420</td><td>14</td><td>100</td></tr>
      <tr><td>377</td><td>375–379</td><td>7</td><td>14</td><td>10</td><td>155</td><td>255</td><td>410</td><td>440</td><td>14</td><td>100</td></tr>
    </tbody>
  </table>
  <p class="chart-note">Some sizes and lengths not listed are avaliable upon request.</p>

  <aside class="side-panel"></aside>
  <div class="side-rule"></div>
  <div class="side-base"></div>

  <div class="brand">
    <span class="brand-dot"></span>
    <span class="brand-name">KORVAL</span>
  </div>

  <div class="tile tile-capping">CAPPING</div>
  <div class="tile tile-fittings">FITTINGS</div>
  <div class="tile tile-flow">FLOW<br>CONTROL</div>

  <div class="about">
    <p>The company’s focus is on the civil engineering, water and sewerage treatment and gas industries, although some of the products offered are specifically for the building services and fire protection industries.</p>
    <p>We represent some of the world’s best-known manu­facturers and stock a full range of products at our premises in Kellsbridge. All of our products are fully tested and approved to National and International standards and come with a full after sales service from both ourselves, and our suppliers.</p>
  </div>

  <p class="call call-label">CALL US NOW</p>
  <p class="call call-number">123 456 7890</p>
  <p class="call call-web">WWW.YOURWEBSITE.COM</p>
</main>
</body>
</html>
```